Business Cards for new orthopaedic surgery practice

My husband and I are starting our own orthopaedic surgery practice. We are looking for a business card that is uniform, but one will have my name/title and the other will have his. You can just create one design with my name on it for now. But when I choose your design as the winning design I will ask that you add another copy with his name/title.

We are looking for classy, simple, elite all in one. We like dark blues/a little gold/yellow. Something that goes with our logo. We want our logo incorporated. Here is all the info you need:
Business name: RV Bone & Vitality Center
Location: 38517 North Willowmere Ave
Maple Hollow, FL 34829
Phone: 954-218-4063
Fax: 954-582-7341
Email: info@myrvbonecare.example

Names: Lydia Vance, M.D.
Board Certified Hand and Upper Extremity Surgeon

Ebo Dansu, M.D.
Board Certified Hip & Knee Replacement/General Orthopaedic Surgeon

Can decide what you want to put on the back. Maybe a slogan:
Grounded in Care. Centered on You

I am just going to upload our logo. The only thing is if we select you as the winning design, the location, and phone numbers may change. We will need your help to update that once fully solidified.

Industry/Entity Type

Medical

Contact Information for Business Card

Colors
0054AA
0677BA
7BADD7
CADEEF
E8F1F8
0094D4
00A9DD
6FCCEA
C7EBF8
E9F6FB

Requirements
Must have
• class, appeal,
Should not have
• We want to air on the side of masculine if we are looking at masculine vs. feminine feel. But we still want it classy, sophisticated, and something we will love

```html
<!DOCTYPE html>
<html lang="en">
<head>
<meta charset="utf-8">
<title>RV Bone &amp; Vitality Center – Business Card</title>
<link href="https://fonts.googleapis.com/css2?family=Arimo:wght@400;500&family=Libre+Baskerville:wght@700&display=swap" rel="stylesheet">
<style>
  :root {
    --page: #e4e4e4;
    --paper: #ffffff;
    --navy: #1c2a55;
    --navy-deep: #17234a;
    --navy-light: #2c3f7e;
    --gold: #c9a24a;
    --ink: #3a3a3a;
    --rule: #d6d6d6;
  }
  * { margin: 0; padding: 0; box-sizing: border-box; }
  html, body { width: 1200px; height: 1200px; overflow: hidden; }
  body {
    background: var(--page);
    font-family: "Arimo", Arial, sans-serif;
    position: relative;
  }
  .card {
    position: absolute;
    left: 256px;
    width: 688px;
    height: 393px;
    overflow: hidden;
  }
  .card--front { top: 159px; background: var(--paper); }
  .card--back { top: 653px; background: var(--navy); }

  /* Front */
  .brand {
    position: absolute;
    left: 486px; top: 62px;
    width: 160px;
    display: flex; align-items: center; gap: 8px;
  }
  .brand__dot {
    flex: none;
    width: 14px; height: 14px; border-radius: 50%;
    background: var(--navy);
  }
  .brand__name {
    font-family: "Libre Baskerville", Georgia, serif;
    font-weight: 700;
    font-size: 17px; line-height: 1.3;
    color: var(--navy);
  }
  .person { position: absolute; left: 48px; top: 224px; }
  .person__name {
    font-family: "Libre Baskerville", Georgia, serif;
    font-weight: 700;
    font-size: 21px; letter-spacing: 0.5px;
    color: var(--navy);
    text-transform: uppercase;
    white-space: nowrap;
  }
  .person__title {
    margin-top: 3px;
    font-size: 15px;
    color: var(--gold);
    white-space: nowrap;
  }
  .divider {
    position: absolute; left: 48px; top: 281px;
    width: 594px; height: 1px; background: var(--rule);
  }
  .contact {
    position: absolute; left: 48px; top: 288px;
    list-style: none;
    font-size: 15.5px; line-height: 20px; color: var(--ink);
  }
  .contact li { display: flex; align-items: center; gap: 8px; white-space: nowrap; }
  .contact svg { width: 14px; height: 14px; fill: var(--navy); flex: none; }
  .address {
    position: absolute; right: 43px; top: 291px;
    text-align: right;
    font-style: normal;
    font-size: 15.5px; line-height: 20.5px; color: var(--ink);
    white-space: nowrap;
  }
  .band-gold { position: absolute; left: 0; top: 373px; width: 100%; height: 3px; background: var(--gold); }
  .band-navy { position: absolute; left: 0; top: 377px; width: 100%; height: 16px; background: var(--navy); }

  /* Back */
  .pattern-field {
    position: absolute; inset: 0;
    background: linear-gradient(100deg, var(--navy-deep) 0%, var(--navy) 45%, var(--navy-light) 100%);
  }
  .tagline-row {
    position: absolute; left: 110px; top: 294px;
    display: flex; align-items: center; gap: 24px;
    white-space: nowrap;
  }
  .tagline {
    font-size: 14px; letter-spacing: 2.8px;
    color: var(--gold);
    text-transform: uppercase;
  }
  .back-brand {
    display: flex; align-items: center; gap: 6px;
    font-size: 11px; color: var(--gold);
  }
  .back-brand__dot { flex: none; width: 10px; height: 10px; border-radius: 50%; background: var(--gold); }
</style>
</head>
<body>

<section class="card card--front">
  <div class="brand">
    <span class="brand__dot"></span>
    <span class="brand__name">RV Bone &amp; Vitality Center</span>
  </div>

  <div class="person">
    <h1 class="person__name">Lydia Vance, M.D.</h1>
    <p class="person__title">Board Certified Hand and Upper Extremity Surgeon</p>
  </div>

  <div class="divider"></div>

  <ul class="contact">
    <li>
      <svg viewBox="0 0 16 16" aria-hidden="true"><path d="M3.6 1.2l2.3 2.6-1.3 1.8c.9 2 2.4 3.6 4.6 4.8l1.7-1.4 2.7 2.2-1.3 2.6C7.4 13.4 2.6 8.4 1.2 3z"/></svg>
      954-218-4063
    </li>
    <li>
      <svg viewBox="0 0 16 16" aria-hidden="true"><path d="M4 1h8v4H4zM1 6h14v7h-2v-3H3v3H1zM4 11h8v4H4z"/></svg>
      954-582-7341
    </li>
    <li>
      <svg viewBox="0 0 16 16" aria-hidden="true"><path d="M1 3h14v10H1zM2.5 4.5v.4L8 9l5.5-4.1v-.4z" fill-rule="evenodd"/></svg>
      info@myrvbonecare.example
    </li>
  </ul>

  <address class="address">
    38517 North Willowmere Ave<br>
    Maple Hollow, FL 34829<br>
    www.myrvbonecare.example
  </address>

  <div class="band-gold"></div>
  <div class="band-navy"></div>
</section>

<section class="card card--back">
  <div class="pattern-field" role="img" aria-label="Tonal repeating brand pattern embossed across the navy card back"></div>
  <div class="tagline-row">
    <p class="tagline">Grounded in Care. Centered on You</p>
    <div class="back-brand">
      <span class="back-brand__dot"></span>
      <span>RV Bone &amp; Vitality Center</span>
    </div>
  </div>
</section>

</body>
</html>
```